Velk Partners Building Business Cards

We need a business card that reflects our business as "Solar Experts" in San Diego. Browse our website www.velkpartners.example our License needs to be displayed as "CSLB# 3867140" our phone number is (619) 555-0187

Save thousands on your electric bills and increase the value of your home while helping to protect the environment. Our solar installation experts will help you design the system that's right for you, using only the highest quality equipment that will look great and give you ideal performance. Our goal is to make you energy independent, and get your electric bill to 0.

Paul Osterby
(619) 555-0187
paul@velkpartners.example

Target Market(s)

Home owners in san diego looking for solar

Industry/Entity Type

Solar Energy

Contact Information for Business Card

Paul Osterby
(619) 555-0187
paul@velkpartners.example

Font styles to use
Other font styles liked:
• Use our logo font

Requirements
Must have
• License needs to be displayed as "CSLB# 3867140" our phone number is (619) 555-0187
Nice to have
• Real images of rooftop home solar in san diego
Should not have
• our business address

```html
<!DOCTYPE html>
<html lang="en">
<head>
<meta charset="utf-8">
<title>Velk Partners Building – Business Cards</title>
<link rel="stylesheet" href="https://fonts.googleapis.com/css2?family=Open+Sans:wght@400;600;700&display=swap">
<style>
  :root {
    --navy: #1f3f80;
    --sun: #f6b21c;
    --sun-light: #fbd25a;
    --paper: #ffffff;
    --ink-grey: #5c5c5c;
    --backdrop: #ecebe7;
  }
  * { margin: 0; padding: 0; box-sizing: border-box; }
  html, body { width: 1200px; height: 950px; overflow: hidden; }
  body {
    background: var(--backdrop);
    font-family: "Open Sans", Arial, sans-serif;
    position: relative;
  }
  .card {
    position: absolute;
    top: 178px;
    width: 340px;
    height: 595px;
    background: var(--paper);
    box-shadow: 0 6px 18px rgba(0,0,0,0.18);
    overflow: hidden;
  }
  .card--front { left: 220px; }
  .card--back { left: 640px; }

  /* Front */
  .person {
    position: absolute;
    top: 40px;
    right: 44px;
  }
  .person__name {
    color: var(--navy);
    font-weight: 700;
    font-size: 27px;
    line-height: 1.15;
  }
  .person__role {
    color: var(--sun);
    font-weight: 400;
    font-size: 19px;
    margin-top: 2px;
  }
  .hero-art {
    position: absolute;
    top: 120px;
    left: 0;
    width: 340px;
    height: 200px;
    background: linear-gradient(180deg, var(--paper) 0%, var(--sun-light) 30%, var(--sun) 60%, var(--navy) 100%);
  }
  .front-band {
    position: absolute;
    left: 0; right: 0;
    top: 320px;
    bottom: 0;
    background: var(--navy);
  }
  .contact {
    position: absolute;
    left: 0; right: 0;
    bottom: 78px;
    color: var(--paper);
    font-size: 16px;
    text-align: center;
    list-style: none;
  }
  .contact li {
    display: flex;
    align-items: center;
    justify-content: center;
    gap: 7px;
    line-height: 1.6;
  }
  .contact .license { margin-bottom: 4px; }
  .contact svg { width: 15px; height: 15px; flex: none; }

  /* Back */
  .brand {
    position: absolute;
    top: 265px;
    left: 0; right: 0;
    display: flex;
    align-items: center;
    justify-content: center;
    gap: 10px;
  }
  .brand__dot {
    width: 22px; height: 22px;
    border-radius: 50%;
    background: var(--sun);
  }
  .brand__name {
    color: var(--navy);
    font-weight: 700;
    font-size: 25px;
    letter-spacing: -0.2px;
  }
  .back-web {
    position: absolute;
    bottom: 58px;
    left: 0; right: 0;
    text-align: center;
    color: var(--ink-grey);
    font-size: 13px;
    font-weight: 600;
    letter-spacing: 3px;
  }
</style>
</head>
<body>

<section class="card card--front" aria-label="Business card front">
  <div class="person">
    <p class="person__name">Paul Osterby</p>
    <p class="person__role">CEO/Founder</p>
  </div>

  <div class="hero-art" role="img" aria-label="Illustration of a rising sun over a sweeping wave"></div>
  <div class="front-band" aria-hidden="true"></div>

  <ul class="contact">
    <li class="license">CSLB# 3867140</li>
    <li>
      <svg viewBox="0 0 16 16" aria-hidden="true"><path d="M4 1.5l2.2 3-1.3 1.5c.8 1.8 2.2 3.2 4 4l1.5-1.3 3 2.2-1.2 2.6C7 13.8 2.2 9 1.7 3.8z" fill="var(--sun)"/></svg>
      (619) 555-0187
    </li>
    <li>
      <svg viewBox="0 0 16 16" aria-hidden="true"><rect x="1" y="3" width="14" height="10" rx="1.5" fill="var(--sun)"/><path d="M1.8 4l6.2 5 6.2-5" fill="none" stroke="var(--navy)" stroke-width="1.3"/></svg>
      paul@velkpartners.example
    </li>
    <li>
      <svg viewBox="0 0 16 16" aria-hidden="true"><circle cx="8" cy="8" r="7" fill="var(--sun)"/><path d="M1 8h14M8 1c-3 3.5-3 10.5 0 14M8 1c3 3.5 3 10.5 0 14" fill="none" stroke="var(--navy)" stroke-width="1"/></svg>
      www.velkpartners.example
    </li>
  </ul>
</section>

<section class="card card--back" aria-label="Business card back">
  <div class="brand">
    <span class="brand__dot" aria-hidden="true"></span>
    <span class="brand__name">Velk Partners Building</span>
  </div>
  <p class="back-web">www.velkpartners.example</p>
</section>

</body>
</html>
```